Venture Capital Investment Firm

We are looking to overhaul our existing website (substantially), with only using the same logos (which we can provide).
We are an investment firm that focuses on making loans to late stage technology companies. Our site should ultimately look like other venture capital firms, and look modern and fresh. We have an existing website www.norvellhub.com which this will be replacing, although we will be using a lot of the existing written content, and potentially the numbers of pages we will need, we are not wed to anything else. Please feel free to shoot any questions at any time and thank you in advance for your help!
Websites we like as examples:
https://www.tesmarkfund.com/
https://www.brindlewoodpartners.com/
Target Market(s)
Potential investors who will invest in our firm, as well as potentially companies that are looking to borrow money from us.
Coding
Coded - Design and coding required
Number of Pages Required
5+ page
Colors
Designer to choose colors to be used in the design.
Look and feel

```html
<!DOCTYPE html>
<html lang="en">
<head>
<meta charset="utf-8">
<title>Norvell IP — Investment Partners</title>
<link rel="stylesheet" href="https://fonts.googleapis.com/css2?family=Cinzel:wght@500;700&family=Rubik:wght@400;500;700&family=Fira+Sans:wght@300;400;500&display=swap">
<style>
:root{
  --navy:#0c0a3e;
  --navy-deep:#0a0835;
  --orange:#f06b12;
  --orange-soft:#e98434;
  --ink:#111111;
  --muted:#666a73;
  --grey-light:#f4f4f5;
  --grey-circle:#d9dadf;
  --white:#ffffff;
}
*{box-sizing:border-box;margin:0;padding:0}
html,body{width:1200px;height:2510px;overflow:hidden;background:var(--white)}
body{position:relative;font-family:"Fira Sans",sans-serif;color:var(--ink)}
.abs{position:absolute}

/* hero */
.hero-bg{position:absolute;left:0;top:0;width:1200px;height:680px}
.brand{position:absolute;display:flex;align-items:center;gap:12px}
.brand-mark{width:38px;height:38px;border:2px solid var(--white);border-radius:50%}
.brand-name{font-family:"Cinzel",serif;font-weight:500;font-size:30px;color:var(--white);line-height:1;letter-spacing:.5px}
.brand-sub{font-family:"Fira Sans",sans-serif;font-size:9px;font-weight:500;color:var(--white);letter-spacing:.3px;margin-top:3px}
.nav{position:absolute;top:51px;left:0;font-size:15px;color:var(--white);letter-spacing:.3px}
.nav a{position:absolute;white-space:nowrap;color:var(--white);text-decoration:none}
.nav .active{font-weight:500}
.login{position:absolute;left:946px;top:33px;width:177px;height:52px;background:var(--white);color:var(--ink);font-size:15px;display:flex;align-items:center;justify-content:center;letter-spacing:.3px}
.hero-title{position:absolute;left:0;width:1200px;top:225px;text-align:center;font-family:"Cinzel",serif;font-weight:700;font-size:62px;line-height:63px;color:var(--white);text-shadow:0 3px 8px rgba(0,0,0,.35)}
.hero-sub{position:absolute;left:0;width:1200px;top:366px;text-align:center;font-size:17px;line-height:31px;color:var(--white);letter-spacing:.3px}
.dot{position:absolute;width:15px;height:15px;border-radius:50%;border:2px solid var(--white)}
.dot.on{background:var(--white)}

/* about */
.about-photo{position:absolute;left:98px;top:604px;width:417px;height:417px;background:linear-gradient(135deg,#2a3550 0%,#7c8494 45%,#d9d5cf 100%);box-shadow:0 6px 18px rgba(0,0,0,.15)}
.about-bar{position:absolute;left:77px;top:630px;width:21px;height:365px;background:var(--orange)}
.section-title{font-family:"Rubik",sans-serif;font-weight:500;font-size:36px;line-height:41px;letter-spacing:.3px}
.about-title{position:absolute;left:579px;top:697px}
.about-rule{position:absolute;left:515px;top:802px;width:208px;height:4px;background:var(--orange)}
.about-kicker{position:absolute;left:579px;top:836px;font-size:16px;color:var(--navy);letter-spacing:.3px}
.about-text{position:absolute;left:579px;top:876px;width:540px;font-size:15px;line-height:26px;color:var(--muted);letter-spacing:.2px}
.learn{position:absolute;left:579px;top:998px;font-size:15px;color:var(--orange);display:flex;align-items:center;gap:12px}

/* strategy */
.strategy-navy{position:absolute;left:0;top:1135px;width:600px;height:386px;background:var(--navy)}
.strategy-orange{position:absolute;left:600px;top:1094px;width:600px;height:469px;background:linear-gradient(180deg,#e58741 0%,#e0691f 60%,#d95a10 100%)}
.strategy-frame{position:absolute;left:551px;top:1173px;width:571px;height:308px;border:4px solid var(--white)}
.strategy-title{position:absolute;left:79px;top:1232px;color:var(--white)}
.strategy-text{position:absolute;left:79px;top:1292px;width:440px;font-size:15px;line-height:26px;color:var(--white);letter-spacing:.2px}
.strategy-text p+p{margin-top:16px}
.focus-icon{position:absolute;width:90px;height:90px;border-radius:50%;background:rgba(255,255,255,.22);border:2px solid rgba(255,255,255,.85)}
.focus{position:absolute;left:773px;width:330px;color:var(--white)}
.focus h3{font-family:"Fira Sans",sans-serif;font-weight:400;font-size:18px;letter-spacing:.3px;margin-bottom:4px}
.focus p{font-size:15px;line-height:26px;letter-spacing:.2px}

/* news */
.news-title{position:absolute;left:0;width:1200px;top:1634px;text-align:center}
.card{position:absolute;top:1719px;width:240px;height:302px;background:var(--white);box-shadow:0 2px 10px rgba(0,0,0,.1)}
.card-photo{height:156px}
.card-date{position:absolute;left:18px;top:180px;font-size:14px;color:#8a8d94}
.card-head{position:absolute;left:18px;top:205px;width:210px;font-size:15px;line-height:23px;color:#222}

/* links strip */
.strip{position:absolute;left:0;top:2104px;width:1200px;height:84px;background:var(--grey-light)}
.strip-divider{position:absolute;left:599px;top:2104px;width:2px;height:84px;background:#dcdcdf}
.strip-label{position:absolute;top:2133px;font-family:"Rubik",sans-serif;font-weight:500;font-size:20px;letter-spacing:.3px}
.strip-text{position:absolute;top:2125px;font-size:14px;line-height:21px;color:var(--muted);letter-spacing:.2px}
.strip-arrow{position:absolute;top:2126px;width:41px;height:41px;border:2px solid var(--orange);border-radius:50%;display:flex;align-items:center;justify-content:center}

/* footer */
.footer{position:absolute;left:0;top:2188px;width:1200px;height:322px;background:var(--navy-deep)}
.social{position:absolute;top:2324px;width:41px;height:41px;border-radius:50%;background:var(--white)}
.social.on{background:var(--orange)}
.foot-h{position:absolute;font-family:"Rubik",sans-serif;font-weight:500;font-size:14px;color:var(--white);letter-spacing:.5px}
.foot-t{position:absolute;font-size:14px;line-height:26px;color:#d5d6e2;letter-spacing:.3px}
.foot-rule{position:absolute;left:0;top:2427px;width:1200px;height:1px;background:rgba(255,255,255,.12)}
.copyright{position:absolute;left:0;width:1200px;top:2458px;text-align:center;font-size:14px;color:#7d7f99;letter-spacing:.3px}
</style>
</head>
<body>

<!-- hero -->
<svg class="hero-bg" viewBox="0 0 1200 680" role="img" aria-label="Business people meeting in an office, blurred, with orange overlay">
  <defs>
    <linearGradient id="heroGrad" x1="0" y1="0" x2="1" y2="0.3">
      <stop offset="0" stop-color="#2c2a63"/>
      <stop offset="0.35" stop-color="#6a5277"/>
      <stop offset="0.65" stop-color="#c9774a"/>
      <stop offset="1" stop-color="#f07a25"/>
    </linearGradient>
  </defs>
  <polygon points="0,0 1200,0 1200,594 0,677" fill="url(#heroGrad)"/>
</svg>

<div class="brand" style="left:78px;top:34px">
  <span class="brand-mark"></span>
  <div>
    <div class="brand-name">NORVELL IP</div>
    <div class="brand-sub">INVESTMENT PARTNERS, LLC</div>
  </div>
</div>

<nav class="nav">
  <a class="active" style="left:393px">HOME</a>
  <a style="left:471px">STRATEGY</a>
  <a style="left:585px">ABOUT US</a>
  <a style="left:700px">TEAM</a>
  <a style="left:773px">NEWS</a>
  <a style="left:846px">CONTACT</a>
</nav>
<div class="login">INVESTORS LOGIN</div>

<h1 class="hero-title">GROW YOUR BUSINESS<br>WITH NORVELL IP</h1>
<p class="hero-sub">WE ARE A GLOBAL STRUCTURED CREDIT INVESTMENT FIRM FOCUSED<br>ON THE HEALTHCARE AND TECHNOLOGY INDUSTRIES</p>
<span class="dot on" style="left:964px;top:539px"></span>
<span class="dot" style="left:995px;top:539px"></span>
<span class="dot" style="left:1026px;top:539px"></span>

<!-- about -->
<svg class="abs" style="left:950px;top:565px" width="110" height="110" viewBox="0 0 110 110" aria-hidden="true">
  <circle cx="55" cy="55" r="55" fill="var(--grey-circle)"/>
</svg>
<svg class="abs" style="left:0;top:560px" width="1200" height="120" viewBox="0 0 1200 120" aria-hidden="true">
  <polygon points="0,117 1200,34 1200,0 0,0" fill="none"/>
</svg>
<div class="about-bar"></div>
<div class="about-photo" role="img" aria-label="Colleagues reviewing financial charts on paper and a tablet"></div>
<h2 class="section-title about-title">NORVELL IP STARTED WITH<br>A BIG IDEA</h2>
<div class="about-rule"></div>
<p class="about-kicker">FINANCE PROVEN INNOVATION WITH A DIFFERENT APPROACH</p>
<p class="about-text">Norvell IP is a private investment firm unique in its dual focus on life science and technology credit opportunities.&nbsp; Our ambidextrous appro -ach to investing reflects a broad recognition and appreciation for the critical role intellectual property plays in the successful</p>
<div class="learn">LEARN MORE
  <svg width="28" height="12" viewBox="0 0 28 12" aria-hidden="true"><path d="M0 6H26M20 1l6 5-6 5" fill="none" stroke="var(--orange)" stroke-width="2"/></svg>
</div>

<!-- strategy -->
<div class="strategy-navy"></div>
<div class="strategy-orange" role="img" aria-label="City skyline with orange overlay"></div>
<div class="strategy-frame"></div>
<h2 class="section-title strategy-title">OUR STRATEGY</h2>
<div class="strategy-text">
  <p>We are a global structured credit investment firm focused on the healthcare and technology industries.</p>
  <p>Our focus spans the life science and technology industries, two sectors where intellectual property (IP) is an integral driver of asset and enterprise value.</p>
</div>
<div class="focus-icon" style="left:651px;top:1212px"></div>
<div class="focus" style="top:1210px">
  <h3>LIFE SCIENCES</h3>
  <p>We have a long track record of partnering with companies and investors that create and commercialize life science products.</p>
</div>
<div class="focus-icon" style="left:651px;top:1348px"></div>
<div class="focus" style="top:1345px">
  <h3>TECHNOLOGY</h3>
  <p>We uniquely offer sizeable and flexible structured credit financing solutions to innovative technology companies.</p>
</div>

<!-- news -->
<h2 class="section-title news-title">NORVELL IP NEWS</h2>
<article class="card" style="left:77px">
  <div class="card-photo" role="img" aria-label="Hand holding a phone beside a cup of coffee" style="background:linear-gradient(135deg,#3b3530,#cfc7bd)"></div>
  <div class="card-date">July 2015</div>
  <div class="card-head">Norvell IP closes inaugural $100,000,000 investment vehicle</div>
</article>
<article class="card" style="left:346px">
  <div class="card-photo" role="img" aria-label="Two businessmen working at a laptop" style="background:linear-gradient(135deg,#8fa0b0,#3a3f4a)"></div>
  <div class="card-date">April 2016</div>
  <div class="card-head">Halvard Semiconductor acquired by Lumatrix for $55,000,000</div>
</article>
<article class="card" style="left:615px">
  <div class="card-photo" role="img" aria-label="Hands pointing at charts on a tablet" style="background:linear-gradient(135deg,#d8d3c9,#4a4a4f)"></div>
  <div class="card-date">Oct. 2016</div>
  <div class="card-head">Norvell IP completes $22,000,000 structured debt investment in Pollwise</div>
</article>
<article class="card" style="left:883px">
  <div class="card-photo" role="img" aria-label="Team shaking hands across an office table" style="background:linear-gradient(135deg,#e4e2de,#8a4a3c)"></div>
  <div class="card-date">April 2018</div>
  <div class="card-head">Norvell IP completes structured debt investment in Trailnote</div>
</article>

<!-- links strip -->
<div class="strip"></div>
<div class="strip-divider"></div>
<div class="strip-label" style="left:79px">INVESTORS</div>
<p class="strip-text" style="left:235px">Lorem ipsum dolor consectetur<br>dolore magna aliqua.</p>
<div class="strip-arrow" style="left:492px"><svg width="10" height="14" viewBox="0 0 10 14" aria-hidden="true"><path d="M2 1l6 6-6 6" fill="none" stroke="var(--orange)" stroke-width="1.8"/></svg></div>
<div class="strip-label" style="left:669px">OUR TEAM</div>
<p class="strip-text" style="left:815px">Lorem ipsum dolor consectetur<br>dolore magna aliqua.</p>
<div class="strip-arrow" style="left:1082px"><svg width="10" height="14" viewBox="0 0 10 14" aria-hidden="true"><path d="M2 1l6 6-6 6" fill="none" stroke="var(--orange)" stroke-width="1.8"/></svg></div>

<!-- footer -->
<footer class="footer"></footer>
<div class="brand" style="left:78px;top:2252px">
  <span class="brand-mark"></span>
  <div>
    <div class="brand-name" style="font-size:24px">NORVELL IP</div>
    <div class="brand-sub" style="font-size:7px">INVESTMENT PARTNERS, LLC</div>
  </div>
</div>
<span class="social on" style="left:76px" aria-label="Social link"></span>
<span class="social" style="left:123px" aria-label="Social link"></span>
<span class="social" style="left:170px" aria-label="Social link"></span>
<span class="social" style="left:217px" aria-label="Social link"></span>

<div class="foot-h" style="left:348px;top:2250px">GENERAL INQUIRIES</div>
<div class="foot-t" style="left:348px;top:2272px">inquiries@norvellip.com</div>
<div class="foot-h" style="left:348px;top:2323px">MEDIA INQUIRIES</div>
<div class="foot-t" style="left:348px;top:2345px">media@norvellip.com</div>

<div class="foot-h" style="left:617px;top:2250px">TRANSACTION OPPORTINITIES</div>
<div class="foot-t" style="left:617px;top:2272px">invopps@norvellip.com</div>
<div class="foot-h" style="left:617px;top:2323px">CAREERS</div>
<div class="foot-t" style="left:617px;top:2345px">career@norvellip.com</div>

<div class="foot-h" style="left:885px;top:2250px">ADDRESS</div>
<div class="foot-t" style="left:885px;top:2272px">2140 Keller Avenue #402<br>Bayfield, CA&nbsp; 94610</div>

<div class="foot-rule"></div>
<p class="copyright">© 2019 Norvell IP Investment Partners LLC.&nbsp; All Rights Reserved.</p>

</body>
</html>
```